Lantern Petals Website v.1 - attract floral shop franchisees

I need a simple information website for my new business. We are a franchisor of flower shops. The overall purpose of the website is to promote the company and the service, especially to potential franchisees and retailers. Only about 4 pages are required including homepage, About, For Supermarkets, For Franchisees, and Contact. No special functions are required except the site will have two separate inquiry forms that must be filled out online and submitted via automated email. Similarly, an email form should be linked from the Contact page. I have a logo and business cards designed by ArtMingle, and I would like the site to have a consistent color scheme and style. The key to design will be to express the joy and love associated with flowers and floral bouquets.
IMPORTANT - I will be exporting the website design to Wordpress CMS in a site hosted by HostNimbus. For smooth integration into WordPress hosted by HostNimbus, the designer should build the site using a WordPress-friendly format. Ideally, they should use HTML, CSS, and PHP. Creating a custom theme or using a page builder that exports to WordPress-compatible files is best. This ensures the site can be easily imported and managed within WordPress.

Target Market(s)

Potential franchisees (existing florists or creative types who might like to own a floral business) and supermarkets who might want us to run their floral department

Industry/Entity Type

Floral retailing

Requirements
Must have
• A brand theme that is beautiful, consistent throughout and builds on the logo design
Nice to have
• Show gender and ethnic diversity in customers and florists. Pictures of happy florists (for franchisees) and pictures of amazing floral department displays (for supermarkets)

```html
<!DOCTYPE html>
<html lang="en">
<head>
<meta charset="utf-8">
<title>Lantern Petals</title>
<link href="https://fonts.googleapis.com/css2?family=Pinyon+Script&family=Poppins:wght@400;500&display=swap" rel="stylesheet">
<style>
:root{
  --cream:#fdf6ec;
  --orange:#f0ad2c;
  --green:#2e9e5b;
  --ink:#2b2b2b;
  --muted:#6d6a66;
  --white:#ffffff;
  --script:"Pinyon Script", cursive;
  --sans:"Poppins", sans-serif;
}
html,body{margin:0;padding:0;overflow:hidden;background:var(--cream);}
.page{position:relative;width:1200px;height:4331px;overflow:hidden;background:var(--cream);font-family:var(--sans);color:var(--ink);}
.abs{position:absolute;}
.btn{position:absolute;display:flex;align-items:center;justify-content:center;background:var(--orange);border-radius:20px;font-family:var(--sans);font-size:12px;letter-spacing:3px;color:var(--ink);text-transform:uppercase;}
.script-title{position:absolute;font-family:var(--script);color:var(--ink);font-weight:400;margin:0;line-height:1;white-space:nowrap;}
.body-text{position:absolute;margin:0;font-size:12.5px;line-height:20px;color:var(--muted);}

/* header */
.brand{left:25px;top:30px;display:flex;align-items:center;gap:10px;}
.brand-dot{width:34px;height:34px;border-radius:50%;background:var(--orange);}
.brand-name{font-family:var(--sans);font-weight:500;font-size:22px;color:var(--orange);}
.nav a{position:absolute;top:57px;font-size:13px;letter-spacing:3px;color:var(--ink);text-decoration:none;white-space:nowrap;}
.nav-contact{left:983px;top:45px;width:152px;height:39px;}

/* hero */
.hero-title{left:74px;top:220px;font-size:60px;}
.hero-text{left:74px;top:300px;width:455px;}
.hero-btn{left:74px;top:427px;width:139px;height:39px;}

/* backgrounds */
.bg-floral{left:0;top:700px;width:1200px;height:1540px;background:radial-gradient(circle at 20% 30%,#f6e5df 0,transparent 40%),radial-gradient(circle at 80% 60%,#f5ecd8 0,transparent 45%),linear-gradient(180deg,#f7efe2,#f4ece0);}
.bg-footer{left:0;top:3700px;width:1200px;height:631px;background:radial-gradient(circle at 85% 20%,#f3e6d2 0,transparent 45%),linear-gradient(180deg,#f8f0e3,#f6eee2);}
.wave{position:absolute;left:0;width:1200px;}

/* about */
.about-title{left:563px;top:930px;font-size:52px;}
.about-text{left:560px;top:1002px;width:545px;font-size:12px;}
.about-btn{left:560px;top:1372px;width:153px;height:40px;}
.ornament{width:80px;height:140px;border-radius:30px;background:linear-gradient(180deg,#cfe6cf,#f3e5c2);opacity:.7;}

/* partner */
.partner-title{left:92px;top:1610px;font-size:52px;}
.partner-text{left:92px;top:1690px;width:545px;font-size:15.5px;line-height:25.5px;}
.partner-badge{left:106px;top:1905px;width:76px;height:70px;background:#e3ddd6;}

/* cards */
.card{position:absolute;top:2495px;width:423px;height:447px;background:var(--white);}
.card-photo{width:423px;height:221px;}
.card-title{left:34px;top:252px;font-size:40px;}
.card-text{left:33px;top:308px;width:370px;font-size:12px;}
.card-btn{left:33px;top:388px;width:135px;height:34px;font-size:11px;}

/* gallery */
.gallery-title{left:0;width:1200px;text-align:center;top:3010px;font-size:60px;}
.tile{position:absolute;width:232px;height:183px;}
.gallery-btn{left:551px;top:3584px;width:135px;height:34px;font-size:10px;letter-spacing:.5px;}

/* footer */
.footer-title{top:3895px;font-size:44px;}
.footer-link{position:absolute;left:99px;font-size:15px;letter-spacing:3.5px;color:var(--ink);text-decoration:none;white-space:nowrap;}
.contact-row{position:absolute;left:358px;display:flex;align-items:center;gap:14px;font-size:15px;white-space:nowrap;}
.icon-ring{width:36px;height:36px;border-radius:50%;border:2px solid var(--green);display:flex;align-items:center;justify-content:center;}
.newsletter{left:672px;top:3887px;width:454px;height:279px;background:var(--white);}
.newsletter-title{left:46px;top:30px;font-size:44px;}
.email-field{position:absolute;left:26px;top:113px;width:282px;height:48px;border:1.5px solid var(--ink);border-radius:26px;box-sizing:border-box;padding-left:34px;display:flex;align-items:center;font-size:13px;color:var(--muted);}
.subscribe{position:absolute;left:26px;top:186px;width:284px;height:52px;border-radius:26px;background:var(--green);color:var(--white);display:flex;align-items:center;justify-content:center;font-size:16px;letter-spacing:4px;}
.newsletter-photo{position:absolute;left:320px;top:63px;width:131px;height:210px;background:linear-gradient(180deg,#f6dce3,#e7efe9);}
.copyright{left:0;width:1200px;text-align:center;top:4254px;font-size:14px;}
</style>
</head>
<body>
<div class="page">

  <!-- header -->
  <div class="abs brand"><span class="brand-dot"></span><span class="brand-name">Lantern Petals</span></div>
  <nav class="nav">
    <a style="left:270px">HOME</a>
    <a style="left:368px">ABOUT</a>
    <a style="left:479px">FOR SUPERMARKETS</a>
    <a style="left:726px">FOR FRANCHISEES</a>
  </nav>
  <div class="btn nav-contact">Contact</div>

  <!-- hero -->
  <h1 class="script-title hero-title">Lantern Petals</h1>
  <p class="body-text hero-text">Fresh flowers convey beauty and love, and in our view should become something every person regularly enjoys. Lantern Petals is an entrepreneurial company created to make top quality fresh flowers and professionally-designed bouquets accessible to every consumer at affordable prices.</p>
  <div class="btn hero-btn">Contact</div>

  <svg class="abs" style="left:626px;top:140px" width="250" height="290" viewBox="0 0 250 290" role="img" aria-label="Photo of a colourful flower display">
    <defs><linearGradient id="gPink" x1="0" y1="0" x2="1" y2="1"><stop offset="0" stop-color="#4a3a36"/><stop offset=".5" stop-color="#d9708f"/><stop offset="1" stop-color="#5d7a3a"/></linearGradient></defs>
    <polygon points="125,3 247,72 247,218 125,287 3,218 3,72" fill="none" stroke="var(--green)" stroke-width="4" stroke-dasharray="10 7"/>
    <polygon points="125,20 232,82 232,208 125,270 18,208 18,82" fill="url(#gPink)"/>
  </svg>
  <svg class="abs" style="left:881px;top:135px" width="250" height="290" viewBox="0 0 250 290" role="img" aria-label="Photo of a florist at work">
    <defs><linearGradient id="gShop" x1="0" y1="0" x2="1" y2="1"><stop offset="0" stop-color="#3b302b"/><stop offset=".5" stop-color="#8a8f99"/><stop offset="1" stop-color="#b55a5a"/></linearGradient></defs>
    <polygon points="125,3 247,72 247,218 125,287 3,218 3,72" fill="none" stroke="var(--green)" stroke-width="4" stroke-dasharray="10 7"/>
    <polygon points="125,20 232,82 232,208 125,270 18,208 18,82" fill="url(#gShop)"/>
  </svg>
  <svg class="abs" style="left:767px;top:360px" width="250" height="290" viewBox="0 0 250 290" role="img" aria-label="Photo of a bouquet of roses and hydrangeas">
    <defs><linearGradient id="gBouquet" x1="0" y1="0" x2="1" y2="1"><stop offset="0" stop-color="#5a4a40"/><stop offset=".5" stop-color="#ecefe6"/><stop offset="1" stop-color="#c0344a"/></linearGradient></defs>
    <polygon points="125,3 247,72 247,218 125,287 3,218 3,72" fill="none" stroke="var(--green)" stroke-width="4" stroke-dasharray="10 7"/>
    <polygon points="125,20 232,82 232,208 125,270 18,208 18,82" fill="url(#gBouquet)"/>
  </svg>

  <!-- floral backdrop -->
  <div class="abs bg-floral" role="img" aria-label="Faint backdrop photo of soft flowers"></div>

  <svg class="wave" style="top:585px" height="210" viewBox="0 0 1200 210" preserveAspectRatio="none">
    <path d="M0,8 C250,0 420,70 650,110 C850,145 1050,120 1200,95 L1200,100 C1050,150 870,170 650,150 C420,128 260,80 0,95 Z" fill="var(--orange)"/>
    <path d="M0,100 C200,90 420,105 580,148 C420,140 200,150 0,205 Z" fill="var(--green)"/>
  </svg>

  <!-- about -->
  <div class="abs ornament" style="left:80px;top:805px" role="img" aria-label="Small bee ornament with dotted flight path"></div>
  <svg class="abs" style="left:66px;top:932px" width="412" height="472" viewBox="0 0 412 472" role="img" aria-label="Photo of the founder holding bright bouquets">
    <defs><linearGradient id="gFounder" x1="0" y1="0" x2="1" y2="1"><stop offset="0" stop-color="#a9b6a4"/><stop offset=".5" stop-color="#8b93a3"/><stop offset="1" stop-color="#e9c63a"/></linearGradient></defs>
    <polygon points="206,3 409,120 409,352 206,469 3,352 3,120" fill="none" stroke="var(--green)" stroke-width="4" stroke-dasharray="10 7"/>
    <polygon points="206,24 390,130 390,342 206,448 22,342 22,130" fill="url(#gFounder)"/>
  </svg>
  <h2 class="script-title about-title">About</h2>
  <div class="body-text about-text">
    <p style="margin:0 0 20px">Professional florists typically sell the finest quality stems, design the most beautiful bouquets and provide the finest customer service, but their costs – of floral products, retail spaces, labor and marketing – force them to pass high prices along to customers. Supermarket flower departments benefit from high customer footfall, economies of scale and low pricing, but their quality of stems and bouquets is typically poor, staffing is limited, and staff turnover is high which can result in inefficiency, wastage, poorly merchandised selections and limited service.</p>
    <p style="margin:0">Lantern Petals brings the best of professional florists and supermarkets together for the benefit of consumers. It supports a national network of owner-operator franchisees, who in many cases are multi-site professional florists, with comprehensive services to enhance franchise profitability. Lantern Petals works with some of the country's largest and most progressive supermarkets to provide franchisee ownership and operation of their strategically important floral departments. Supermarkets find that Lantern Petals is able to improve their financial outcomes, provide attentive customer service and satisfaction, and lift the quality of the entire store environment.</p>
  </div>
  <div class="btn about-btn">Contact</div>

  <!-- partner -->
  <div class="abs ornament" style="left:1030px;top:1440px" role="img" aria-label="Small bee ornament with dotted flight path"></div>
  <h2 class="script-title partner-title">Frostvale</h2>
  <p class="body-text partner-text">Lantern Petals operates in partnership with Frostvale Group, the leading franchisor of sushi stations and pre-packaged fruit &amp; vegetable departments to supermarkets across the United States and United Kingdom. Lantern Petals' combination of floral and supermarket franchising expertise guarantees that consumers, franchisees and supermarket partners each receive exceptional service and value.</p>
  <div class="abs partner-badge"></div>
  <svg class="abs" style="left:710px;top:1572px" width="412" height="472" viewBox="0 0 412 472" role="img" aria-label="Photo of a chocolate fountain beside fruit skewers">
    <defs><linearGradient id="gFruit" x1="0" y1="0" x2="1" y2="1"><stop offset="0" stop-color="#e8c23a"/><stop offset=".5" stop-color="#b2352a"/><stop offset="1" stop-color="#6b3f22"/></linearGradient></defs>
    <polygon points="206,3 409,120 409,352 206,469 3,352 3,120" fill="none" stroke="var(--green)" stroke-width="4" stroke-dasharray="10 7"/>
    <polygon points="206,24 390,130 390,342 206,448 22,342 22,130" fill="url(#gFruit)"/>
  </svg>

  <svg class="wave" style="top:2115px" height="215" viewBox="0 0 1200 215" preserveAspectRatio="none">
    <path d="M1200,0 C950,10 780,75 560,95 C360,115 150,85 0,70 L0,75 C150,110 360,145 560,140 C780,135 950,85 1200,45 Z" fill="var(--orange)"/>
    <path d="M1200,100 C1000,90 780,92 610,150 C780,138 1000,150 1200,210 Z" fill="var(--green)"/>
  </svg>

  <!-- cards -->
  <div class="abs ornament" style="left:70px;top:2470px" role="img" aria-label="Small bee ornament with dotted flight path"></div>
  <div class="abs ornament" style="left:1050px;top:2470px" role="img" aria-label="Small bee ornament with dotted flight path"></div>
  <div class="card" style="left:155px">
    <div class="card-photo" role="img" aria-label="Photo of a supermarket floral department display" style="background:linear-gradient(120deg,#3a4a3a,#c779a8,#e2564a)"></div>
    <h3 class="script-title card-title">For Supermarkets</h3>
    <p class="body-text card-text">Supermarket flower departments benefit from high customer footfall, economies of scale and low pricing. However their quality of stems and bouquets is ...</p>
    <div class="btn card-btn">Read More</div>
  </div>
  <div class="card" style="left:622px">
    <div class="card-photo" role="img" aria-label="Photo of two smiling florists holding flowers" style="background:linear-gradient(120deg,#8c8a6a,#e4d6c8,#b85468)"></div>
    <h3 class="script-title card-title">For Franchisee</h3>
    <p class="body-text card-text">Lantern Petals supports a national network of owner-operator franchisees with comprehensive services to enhance franchise profits.</p>
    <div class="btn card-btn">Read More</div>
  </div>

  <!-- gallery -->
  <h2 class="script-title gallery-title">Gallery</h2>
  <div class="tile" style="left:113px;top:3149px;background:linear-gradient(135deg,#6a5a4e,#e7e9e0,#d0456a)" role="img" aria-label="Bouquet of roses and hydrangeas"></div>
  <div class="tile" style="left:366px;top:3149px;background:linear-gradient(135deg,#4b5a2c,#e8a033,#b7462c)" role="img" aria-label="Orange protea arrangement"></div>
  <div class="tile" style="left:622px;top:3149px;background:linear-gradient(135deg,#4a3a36,#d9708f,#5d7a3a)" role="img" aria-label="Pink flower display in a shop"></div>
  <div class="tile" style="left:876px;top:3149px;background:linear-gradient(135deg,#b1bba8,#8b93a3,#e9c63a)" role="img" aria-label="Florist with yellow and blue bouquets"></div>
  <div class="tile" style="left:116px;top:3350px;background:linear-gradient(135deg,#f3ede4,#d69a2e,#5a3b28)" role="img" aria-label="Person holding sunflowers"></div>
  <div class="tile" style="left:369px;top:3350px;background:linear-gradient(135deg,#2f3a2c,#8a5aa8,#e3e3e3)" role="img" aria-label="Buckets of mixed cut flowers"></div>
  <div class="tile" style="left:624px;top:3350px;background:linear-gradient(135deg,#d8336e,#e25b9c,#3d6b2f)" role="img" aria-label="Close-up of bright pink blooms"></div>
  <div class="tile" style="left:878px;top:3350px;background:linear-gradient(135deg,#2c3a28,#cf6a78,#4b5a3a)" role="img" aria-label="Dark floral arrangement with a pink bloom"></div>
  <div class="btn gallery-btn">View Gallery</div>

  <!-- footer -->
  <div class="abs bg-footer" role="img" aria-label="Faint backdrop photo of flowers"></div>
  <svg class="wave" style="top:3645px" height="210" viewBox="0 0 1200 210" preserveAspectRatio="none">
    <path d="M0,8 C250,0 420,70 650,110 C850,145 1050,120 1200,95 L1200,100 C1050,150 870,170 650,150 C420,128 260,80 0,95 Z" fill="var(--orange)"/>
    <path d="M0,100 C200,90 420,105 580,148 C420,140 200,150 0,205 Z" fill="var(--green)"/>
  </svg>

  <h2 class="script-title footer-title" style="left:76px">About</h2>
  <a class="footer-link" style="top:3986px">HOME</a>
  <a class="footer-link" style="top:4034px">ABOUT</a>
  <a class="footer-link" style="top:4083px">FOR SUPERMARKETS</a>
  <a class="footer-link" style="top:4131px">FOR FRANCHISEE</a>
  <a class="footer-link" style="top:4180px">CONTACT</a>

  <h2 class="script-title footer-title" style="left:363px">Contact</h2>
  <div class="contact-row" style="top:3978px">
    <span class="icon-ring"><svg width="16" height="16" viewBox="0 0 24 24"><path d="M6.6 10.8a15 15 0 0 0 6.6 6.6l2.2-2.2a1 1 0 0 1 1-.25 11.4 11.4 0 0 0 3.6.57 1 1 0 0 1 1 1V20a1 1 0 0 1-1 1A17 17 0 0 1 3 4a1 1 0 0 1 1-1h3.5a1 1 0 0 1 1 1c0 1.25.2 2.450.57 3.6a1 1 0 0 1-.25 1z" fill="var(--green)"/></svg></span>
    <span>+1 555 824 7716</span>
  </div>
  <div class="contact-row" style="top:4037px">
    <span class="icon-ring"><svg width="16" height="16" viewBox="0 0 24 24"><rect x="3" y="6" width="18" height="13" rx="2" fill="var(--green)"/><path d="M3.5 7l8.5 6 8.5-6" fill="none" stroke="#fff" stroke-width="1.6"/></svg></span>
    <span>info@Lantern-Petals.com</span>
  </div>

  <div class="abs newsletter">
    <h2 class="script-title newsletter-title">Newsletter</h2>
    <div class="email-field">Email Address</div>
    <div class="subscribe">SUBSCRIBE NOW</div>
    <div class="newsletter-photo" role="img" aria-label="Photo of a pastel bouquet in a watering can"></div>
  </div>

  <p class="abs copyright" style="margin:0">Copyright 2024 Lantern. All Rights Reserved.</p>
</div>
</body>
</html>
```